Business Card Design Project

This is the first time we use our new logo. We need a business card that we can use both on our institutional corporate relationships and also that works for our staff that deals with consumers directly.

VELUNDA is a new company dedicated to empower consumers and to provide them with the best choices for specialized health care using the latest telemedicine technology (medicine at a distance via videoconference).

We want to print this cards in high quality materials and process. We will like designs that allow us to use UV spot varnish and other techniques that will differentiate us.

We are including Two different versions of Color logos. In addition we are including white over black background logos. Those can be used replacing the black for a color.

Please note this is the first time we will be creating any corporate materials with our new logo and colors.

Target Market(s)

34+ consumers of medium high and high socioeconomic levels.

Industry/Entity Type

Health

Requirements
Must have
• Our logo on its original colors
Should not have
• Any other graphical element or design that is not our logo

```html
<!DOCTYPE html>
<html lang="en">
<head>
<meta charset="utf-8">
<title>VELUNDA Business Card</title>
<link rel="stylesheet" href="https://fonts.googleapis.com/css2?family=Arimo:wght@400;700&display=swap">
<style>
  :root {
    --page-bg: #e4e4e6;
    --card-dark: #2a2a2b;
    --card-dark-edge: #1f1f20;
    --sky-blue: #55b4de;
    --deep-blue: #1f6fae;
    --text-blue: #5fbde6;
    --text-white: #ffffff;
    --shadow: rgba(0, 0, 0, 0.28);
  }
  html, body {
    margin: 0;
    padding: 0;
    width: 1200px;
    height: 987px;
    overflow: hidden;
    background: var(--page-bg);
    font-family: "Arimo", Arial, sans-serif;
  }
  .canvas {
    position: relative;
    width: 1200px;
    height: 987px;
  }
  .card {
    position: absolute;
    width: 700px;
    height: 400px;
    border-radius: 28px;
    background: radial-gradient(ellipse at 40% 30%, #333334 0%, var(--card-dark) 55%, var(--card-dark-edge) 100%);
    box-shadow: 0 14px 30px var(--shadow);
    overflow: hidden;
  }
  .card--back { left: 440px; top: 60px; }
  .card--front { left: 60px; top: 527px; }

  /* Back */
  .back-brand {
    position: absolute;
    left: 0; right: 0; top: 130px;
    display: flex;
    align-items: center;
    justify-content: center;
    gap: 16px;
  }
  .brand-dot {
    width: 26px; height: 26px;
    border-radius: 50%;
    background: var(--sky-blue);
  }
  .brand-name {
    font-weight: 700;
    color: var(--deep-blue);
    letter-spacing: 6px;
  }
  .back-brand .brand-name { font-size: 58px; }
  .back-web {
    position: absolute;
    left: 0; right: 0; top: 230px;
    text-align: center;
    color: var(--text-blue);
    font-size: 22px;
    letter-spacing: 5px;
  }

  /* Front */
  .front-wave {
    position: absolute;
    inset: 0;
    width: 100%;
    height: 100%;
  }
  .front-brand {
    position: absolute;
    left: 150px; top: 36px;
    display: flex;
    align-items: center;
    gap: 14px;
  }
  .front-brand .brand-name { font-size: 52px; }
  .front-brand .brand-dot { width: 22px; height: 22px; }
  .person {
    position: absolute;
    left: 50px; top: 96px;
    color: var(--text-blue);
  }
  .person__name { font-size: 24px; font-weight: 700; }
  .person__title { font-size: 18px; font-weight: 400; }
  .contact-list {
    list-style: none;
    margin: 10px 0 0;
    padding: 0;
    font-size: 17px;
    line-height: 23px;
    color: var(--deep-blue);
  }
  .contact-list li { display: flex; align-items: center; gap: 8px; }
  .contact-list svg { width: 14px; height: 14px; fill: var(--deep-blue); }
  .address {
    position: absolute;
    right: 50px; bottom: 22px;
    text-align: right;
    color: var(--text-white);
    font-size: 22px;
    line-height: 28px;
  }
</style>
</head>
<body>
<main class="canvas">

  <section class="card card--back" aria-label="Card back">
    <div class="back-brand">
      <span class="brand-dot"></span>
      <span class="brand-name">VELUNDA</span>
    </div>
    <div class="back-web">www.velunda.com</div>
  </section>

  <section class="card card--front" aria-label="Card front">
    <svg class="front-wave" viewBox="0 0 700 400" preserveAspectRatio="none">
      <path d="M0 120 C 0 240, 60 262, 200 266 C 420 272, 600 266, 700 262 L 700 400 L 0 400 Z" fill="var(--sky-blue)"/>
      <path d="M10 190 C 30 285, 120 284, 220 284 C 430 290, 600 284, 700 280" fill="none" stroke="var(--card-dark)" stroke-width="4"/>
    </svg>

    <div class="front-brand">
      <span class="brand-dot"></span>
      <span class="brand-name">VELUNDA</span>
    </div>

    <div class="person">
      <div><span class="person__name">Your Name,</span> <span class="person__title">Title</span></div>
      <ul class="contact-list">
        <li><svg viewBox="0 0 16 16"><path d="M3 1h3l1 4-2 1a9 9 0 0 0 5 5l1-2 4 1v3a2 2 0 0 1-2 2C7 15 1 9 1 3a2 2 0 0 1 2-2z"/></svg>012-345-6789</li>
        <li><svg viewBox="0 0 16 16"><path d="M3 1h3l1 4-2 1a9 9 0 0 0 5 5l1-2 4 1v3a2 2 0 0 1-2 2C7 15 1 9 1 3a2 2 0 0 1 2-2z"/></svg>012-345-6789</li>
        <li><svg viewBox="0 0 16 16"><path d="M1 3h14v10H1z M1 3l7 6 7-6" stroke="var(--card-dark)" stroke-width="1"/></svg>name@velunda.com</li>
        <li><svg viewBox="0 0 16 16"><circle cx="8" cy="8" r="7"/></svg>www.velunda.com</li>
      </ul>
    </div>

    <div class="address">
      Street Name<br>
      City Name, State<br>
      City Zip Code
    </div>
  </section>

</main>
</body>
</html>
```